Interior design service, along with home organization, packing, and staging, home and business. As well as staging in conjunction with real estate sales.
Updates

Love many of your designs and will be choosing today. To inform you of the exact details needed, the name of the company is "Flourish by Marnie T" , my phone number and e-,ail need to be included. i also need either description or some sort of bullet points that give an idea of the following:

- Interior design for home and business
- Home organization and packing
- Staging for personal and professional space
- Real estate stagingĀ 

Thank you

Target Market(s)

wide audience, but most importantly people looking for a quality service

Industry/Entity Type

Real Estate

Contact Information for Business Card

Flourish By Marnie T
Marnie Tolvery
(555)687-3914
mtbrisco@postwell.example

Requirements
Must have
• I'm 29 so i want my card to reflect something professional but still fresh. I don't have any specific photos or quotes that Ive included, however I like the card to reflect a personal touch, which is what I'm seeking from this service in the design of my card. Thanks!

```html
<!DOCTYPE html>
<html lang="en">
<head>
<meta charset="utf-8">
<title>Flourish By Marnie T – Business Card</title>
<link rel="stylesheet" href="https://fonts.googleapis.com/css2?family=Federo&family=Tenor+Sans&display=swap">
<style>
  :root {
    --stage: #3b3b3b;
    --card: #262626;
    --gold: #d9b82c;
    --gold-shade: #b89a30;
    --gold-fold: #a88c2c;
    --ink-box: #222222;
  }
  html, body {
    margin: 0;
    padding: 0;
    overflow: hidden;
  }
  .canvas {
    position: relative;
    width: 1200px;
    height: 960px;
    background: var(--stage);
    overflow: hidden;
  }
  .card {
    position: absolute;
    width: 608px;
    height: 358px;
    display: block;
  }
  .card--front { left: 172px; top: 36px; }
  .card--back  { left: 449px; top: 428px; }
  .card-bg { fill: var(--card); }
  .band-bright { fill: var(--gold); }
  .band-shade { fill: var(--gold-shade); }
  .band-fold { fill: var(--gold-fold); }
  .question-box { fill: var(--ink-box); }
  .question {
    font-family: "Tenor Sans", sans-serif;
    font-size: 19px;
    fill: var(--gold);
  }
  .brand-by, .brand-name, .label, .detail, .owner, .services {
    font-family: "Federo", sans-serif;
    fill: var(--gold);
  }
  .brand-by { font-size: 16px; }
  .brand-name { font-size: 42px; stroke: var(--gold); stroke-width: 0.6px; }
  .label { font-size: 21px; }
  .owner { font-size: 17px; }
  .detail { font-size: 19px; }
  .services { font-size: 12px; }
  .divider { fill: var(--gold); }
</style>
</head>
<body>
<main class="canvas">

  <svg class="card card--front" viewBox="0 0 507 298" aria-label="Business card front">
    <rect class="card-bg" width="507" height="298"/>
    <polygon class="band-bright" points="0,55 205,55 205,124 0,124"/>
    <polygon class="band-fold" points="205,55 237,63 237,132 205,124"/>
    <rect class="band-shade" x="237" y="63" width="270" height="69"/>
    <rect class="question-box" x="277" y="65" width="188" height="65"/>
    <text class="question" text-anchor="middle">
      <tspan x="371" y="83">Are you looking</tspan>
      <tspan x="371" y="104">for a</tspan>
      <tspan x="371" y="125">quality service?</tspan>
    </text>
    <text class="brand-by" x="18" y="200">Flourish By,</text>
    <text class="brand-name" x="62" y="244" textLength="415" lengthAdjust="spacingAndGlyphs">Marnie T Marnie Tolvery</text>
  </svg>

  <svg class="card card--back" viewBox="0 0 507 298" aria-label="Business card back">
    <rect class="card-bg" width="507" height="298"/>

    <text class="services" x="18" y="24">• Interior design for home &amp; business   • Home organization &amp; packing</text>
    <text class="services" x="18" y="43">• Staging for personal &amp; professional space   • Real estate staging</text>

    <rect class="band-shade" x="0" y="63" width="272" height="69"/>
    <polygon class="band-fold" points="272,63 305,55 305,124 272,132"/>
    <rect class="band-bright" x="305" y="55" width="202" height="69"/>

    <text class="label" x="255" y="207" text-anchor="end">Name</text>
    <text class="owner" x="255" y="230" text-anchor="end">Marnie T Marnie Tolvery</text>

    <rect class="divider" x="278" y="155" width="5" height="122"/>

    <text class="label" x="295" y="176">Phone</text>
    <text class="detail" x="295" y="202">(555)687-3914</text>
    <text class="label" x="295" y="244">Email</text>
    <text class="detail" x="295" y="268" textLength="200" lengthAdjust="spacingAndGlyphs">mtbrisco@postwell.example</text>
  </svg>

</main>
</body>
</html>
```